Corven Hale Interiors Web Site

We are looking at web site for our start-up company which is located in Abu Dhabi United Arab Emirates. Our main business activity is Interior fit out for high medium to high end projects in residential, corporate and hospitality.
In terms of look and feel the web site should be vibrant yet professional reflecting the artistic/construction nature of our business and built along or allows the following aspects:
- Number of Pages: 8-10 main pages (Including 10 Sub Pages)
- A custom responsive web design compatible with all browsers
- Dynamic (admin panel). CMS
- Anti Spam Online Forms
- Photo & Video Gallery
- Mobile Ready (Iphone,Android)]
- Social Media Integration
- Google Map
- Banner Artworks

```html
<!DOCTYPE html>
<html lang="en">
<head>
<meta charset="utf-8">
<title>Corven Hale Interiors</title>
<link rel="stylesheet" href="https://fonts.googleapis.com/css2?family=Open+Sans:wght@400;600;700&display=swap">
<style>
:root{
  --teal:#1d4b5e;
  --teal-dark:#163a49;
  --navy:#1d3546;
  --text:#555e63;
  --muted:#8a9297;
  --line:#d9dee1;
  --bg:#ffffff;
  --soft:#f3f5f6;
}
*{box-sizing:border-box;margin:0;padding:0}
html,body{width:1200px;height:2568px;overflow:hidden}
body{position:relative;background:var(--bg);font-family:"Open Sans",Arial,sans-serif;color:var(--text)}
.abs{position:absolute}

/* header */
.site-header{left:0;top:0;width:1200px;height:160px;background:#fff}
.brand{left:40px;top:28px;display:flex;align-items:center;gap:14px}
.brand-mark{width:40px;height:40px;background:var(--teal)}
.brand-name{font-size:30px;font-weight:700;color:var(--teal);line-height:1.1}
.brand-sub{left:40px;top:118px;font-size:14px;font-weight:600;color:var(--teal)}
.top-contact{right:70px;top:22px;display:flex;gap:34px;font-size:13px;color:var(--text)}
.top-contact span{display:flex;align-items:center;gap:8px}
.main-nav{left:430px;top:100px;display:flex;gap:6px}
.main-nav a{display:block;padding:11px 20px;font-size:14px;color:var(--text);text-decoration:none}
.main-nav a.active{background:var(--teal);color:#fff}

/* hero */
.hero{left:0;top:160px;width:1200px;height:480px;background:linear-gradient(135deg,#c9c4bc 0%,#ebe8e3 40%,#8f8b86 70%,#d8d3cb 100%)}
.hero-dots{left:576px;top:612px;display:flex;gap:8px}
.hero-dots i{width:10px;height:10px;border-radius:50%;background:#fff;opacity:.6}
.hero-dots i.on{opacity:1;background:var(--teal)}

/* section headings */
.section-title{width:1200px;left:0;text-align:center;font-size:26px;font-weight:600;color:var(--teal)}
.welcome-sub{left:0;top:712px;width:1200px;text-align:center;font-size:14px;color:var(--text)}
.welcome-copy{left:180px;top:738px;width:840px;text-align:center;font-size:12px;line-height:20px;color:var(--muted)}

/* feature cards */
.card{top:800px;width:268px}
.card-img{width:268px;height:140px}
.card h3{margin-top:14px;font-size:16px;font-weight:600;color:var(--teal)}
.card p{margin-top:8px;font-size:12px;line-height:1.6;color:var(--muted);padding-right:30px}
.card-arrow{position:absolute;right:0;bottom:4px}
.card-rule{top:1074px;left:176px;width:848px;height:1px;background:var(--line)}

/* news */
.news{top:1128px;width:268px;display:flex;gap:12px}
.news-date{width:62px;height:72px;background:var(--teal);color:#fff;text-align:center;flex:none}
.news-date b{display:block;font-size:30px;line-height:46px}
.news-date small{display:block;font-size:12px;text-transform:uppercase}
.news p{font-size:13px;line-height:1.5;color:var(--teal)}

/* gallery */
.gallery-band{left:0;top:1300px;width:1200px;height:510px;background:var(--soft)}
.gallery-side{top:1300px;width:176px;height:510px;opacity:.45}
.gallery-grid{left:176px;top:1300px;width:848px;height:510px;display:grid;grid-template-columns:repeat(3,1fr);grid-template-rows:170px 166px 166px;gap:4px}
.tile{position:relative}
.play{position:absolute;left:50%;top:50%;transform:translate(-50%,-50%)}
.gallery-arrow{top:1530px;width:44px;height:44px;border-radius:50%;background:rgba(255,255,255,.85);display:flex;align-items:center;justify-content:center}

/* contact */
.contact-form{left:176px;top:1884px;width:848px}
.row{display:flex;gap:14px;margin-bottom:12px}
.field{flex:1;height:32px;border:1px solid var(--line);font-size:12px;color:var(--muted);padding:8px 12px}
.field.message{height:40px}
.submit{left:550px;top:2062px;width:100px;height:34px;background:var(--teal);color:#fff;font-size:13px;font-weight:600;text-align:center;line-height:34px}

/* map */
.map{left:0;top:2136px;width:1200px;height:268px;background:linear-gradient(120deg,#e8e4da 0%,#d9e1cf 35%,#c8d8e2 60%,#e6e2d8 100%)}

/* footer */
.site-footer{left:0;top:2404px;width:1200px;height:164px;background:var(--navy)}
.footer-links{left:0;top:2436px;width:1200px;text-align:center;font-size:12px;color:#b9c5cd}
.footer-links span{margin:0 14px}
.social{left:530px;top:2468px;display:flex;gap:12px}
.social i{width:32px;height:32px;border-radius:50%;background:#c9d3d9}
.copyright{left:0;top:2520px;width:1200px;text-align:center;font-size:11px;color:#8fa0ab}
.to-top{right:40px;top:2526px;font-size:11px;color:#8fa0ab}
</style>
</head>
<body>

<header class="site-header abs">
  <div class="brand abs"><div class="brand-mark"></div><div class="brand-name">Corven Hale</div></div>
  <div class="brand-sub abs">Corven Hale Interiors</div>
  <div class="top-contact abs">
    <span><svg width="14" height="14" viewBox="0 0 24 24"><path fill="#1d4b5e" d="M6.6 10.8a15 15 0 0 0 6.6 6.6l2.2-2.2c.3-.3.7-.4 1-.2 1.1.4 2.3.6 3.6.6.6 0 1 .4 1 1V20c0 .6-.4 1-1 1A17 17 0 0 1 3 4c0-.6.4-1 1-1h3.5c.6 0 1 .4 1 1 0 1.3.2 2.5.6 3.6.1.3 0 .7-.2 1z"/></svg>+971 2 555 0148</span>
    <span><svg width="16" height="12" viewBox="0 0 16 12"><rect x=".5" y=".5" width="15" height="11" fill="none" stroke="#1d4b5e"/><path d="M.5 .5 8 7l7.5-6.5" fill="none" stroke="#1d4b5e"/></svg>info@corvenhale.ae</span>
  </div>
  <nav class="main-nav abs">
    <a class="active" href="#">Home</a><a href="#">About Us</a><a href="#">Services</a><a href="#">Gallery</a><a href="#">Testimonials</a><a href="#">Contact</a><a href="#">Blog</a>
  </nav>
</header>

<div class="hero abs" role="img" aria-label="Banner photograph of a bright modern living room with white sofas and a wall-mounted television"></div>
<div class="hero-dots abs"><i class="on"></i><i></i><i></i></div>

<h1 class="section-title abs" style="top:670px">Welcome To Corven Hale</h1>
<div class="welcome-sub abs">Style. Comfort. Quality. Selection.</div>
<p class="welcome-copy abs">We deliver interior fit out for residential, corporate and hospitality projects across Abu Dhabi, with careful craft and refined finishes. Our team plans, builds and completes every detail so clients move into calm, bright spaces.</p>

<div class="card abs" style="left:176px">
  <div class="card-img" role="img" aria-label="Photograph of a furnished bedroom interior" style="background:linear-gradient(135deg,#6e5a48,#c9b9a4 60%,#3d3530)"></div>
  <h3>Residential fit out</h3>
  <p>Private homes and villas finished with durable materials and warm detail.</p>
  <svg class="card-arrow" width="22" height="14" viewBox="0 0 22 14"><path d="M0 7h18M12 1l7 6-7 6" fill="none" stroke="#1d4b5e" stroke-width="3"/></svg>
</div>
<div class="card abs" style="left:466px">
  <div class="card-img" role="img" aria-label="Photograph of a dining area with wooden furniture" style="background:linear-gradient(135deg,#8a6a4a,#e2d3bd 55%,#5e4a38)"></div>
  <h3>Corporate workspaces</h3>
  <p>Offices planned for focus and teamwork, delivered on time and budget.</p>
  <svg class="card-arrow" width="22" height="14" viewBox="0 0 22 14"><path d="M0 7h18M12 1l7 6-7 6" fill="none" stroke="#1d4b5e" stroke-width="3"/></svg>
</div>
<div class="card abs" style="left:756px">
  <div class="card-img" role="img" aria-label="Photograph of a colourful lounge with green and pink chairs" style="background:linear-gradient(135deg,#8fc25a,#e7e2ea 50%,#c84f8a)"></div>
  <h3>Hospitality interiors</h3>
  <p>Hotels, lounges and restaurants with bold, welcoming character.</p>
  <svg class="card-arrow" width="22" height="14" viewBox="0 0 22 14"><path d="M0 7h18M12 1l7 6-7 6" fill="none" stroke="#1d4b5e" stroke-width="3"/></svg>
</div>
<div class="card-rule abs"></div>

<h2 class="section-title abs" style="top:1084px">News &amp; Events</h2>
<div class="news abs" style="left:176px"><div class="news-date"><b>30</b><small>Aug</small></div><p>New villa fit out completed on Saadiyat with bespoke joinery throughout.</p></div>
<div class="news abs" style="left:466px"><div class="news-date"><b>21</b><small>Aug</small></div><p>Our team joins the regional design week with a new showroom display.</p></div>
<div class="news abs" style="left:756px"><div class="news-date"><b>20</b><small>Aug</small></div><p>Hotel lobby renovation begins for a boutique property in the capital.</p></div>

<h2 class="section-title abs" style="top:1256px">Our Gallery</h2>
<div class="gallery-band abs"></div>
<div class="gallery-side abs" role="img" aria-label="Faded photograph of a bright lobby interior" style="left:0;background:linear-gradient(135deg,#9fb8b8,#e4ece9)"></div>
<div class="gallery-side abs" role="img" aria-label="Faded photograph of a curved hallway interior" style="left:1024px;background:linear-gradient(135deg,#e4ece9,#9fb8b8)"></div>
<div class="gallery-grid abs">
  <div class="tile" role="img" aria-label="Video still of a red lounge interior" style="background:linear-gradient(135deg,#8a2e2a,#d66a4e 50%,#f0d9c8)">
    <svg class="play" width="46" height="46" viewBox="0 0 46 46"><circle cx="23" cy="23" r="22" fill="rgba(255,255,255,.85)"/><path d="M18 14l14 9-14 9z" fill="#1d4b5e"/></svg>
  </div>
  <div class="tile" role="img" aria-label="Photograph of a pale blue office interior" style="background:linear-gradient(135deg,#aec4d2,#e6eef3 60%,#8aa3b3)"></div>
  <div class="tile" role="img" aria-label="Photograph of decorative vases on a shelf" style="background:linear-gradient(135deg,#c9a57c,#eee3d4 50%,#5a8aa8)"></div>
  <div class="tile" role="img" aria-label="Photograph of an open plan living area" style="background:linear-gradient(135deg,#dcdcd6,#f5f4f0 50%,#9a9a94)"></div>
  <div class="tile" role="img" aria-label="Photograph of a green and white patterned ceiling" style="background:linear-gradient(135deg,#e9efe6,#7fbf5a 55%,#2f6a3a)"></div>
  <div class="tile" role="img" aria-label="Photograph of warm wood panelled restaurant" style="background:linear-gradient(135deg,#6e4a2a,#c7955d 55%,#3b2818)"></div>
  <div class="tile" role="img" aria-label="Photograph of a red bedroom interior" style="background:linear-gradient(135deg,#5e1e22,#b33a3a 55%,#d9b49a)"></div>
  <div class="tile" role="img" aria-label="Photograph of a colourful office with green carpet" style="background:linear-gradient(135deg,#d8dde2,#6fae4a 55%,#c2364a)"></div>
  <div class="tile" role="img" aria-label="Photograph of a playroom with colourful shelving" style="background:linear-gradient(135deg,#e8d4b0,#d76a3a 50%,#4e8ac0)"></div>
</div>
<div class="gallery-arrow abs" style="left:66px"><svg width="14" height="18" viewBox="0 0 14 18"><path d="M11 2 4 9l7 7" fill="none" stroke="#1d4b5e" stroke-width="3"/></svg></div>
<div class="gallery-arrow abs" style="left:1090px"><svg width="14" height="18" viewBox="0 0 14 18"><path d="M3 2l7 7-7 7" fill="none" stroke="#1d4b5e" stroke-width="3"/></svg></div>

<h2 class="section-title abs" style="top:1830px">Contact us</h2>
<form class="contact-form abs">
  <div class="row"><div class="field" style="flex:1">Full Name</div><div class="field" style="flex:1.5">Address</div></div>
  <div class="row"><div class="field">Mail Address</div><div class="field">Phone</div><div class="field">City</div></div>
  <div class="row"><div class="field message">Message</div></div>
</form>
<div class="submit abs">Submit</div>

<div class="map abs" role="img" aria-label="Location map of the office in Abu Dhabi"></div>

<footer class="site-footer abs"></footer>
<div class="footer-links abs"><span>Terms of Service</span><span>Privacy Policy</span><span>Contact</span><span>Sitemap</span></div>
<div class="social abs"><i></i><i></i><i></i><i></i><i></i></div>
<div class="copyright abs">Copyright © 2015 Corven Hale Interiors. All rights reserved.</div>
<div class="to-top abs">TOP</div>

</body>
</html>
```